"Beyond The Grey Harbor" Fictional Book Cover

BEYOND THE GREY HARBOR
By: Derek Falloway

Here's the intro .

"It had been nearly forty years since Tim Ashworth last went to the island from where he was raised. Three months earlier he never would have thought about ever coming back. But life is weird. Things happen quickly and plans change, especially when your very life is at stake. The reason he was going back wasn’t to see old friends...no, no, no. They’re all dead. Of all the kids he grew up with on the island who moved off, he’s the only one still alive. Why?"

Pretty much all just a Lumora book, by the way.

Target Market(s)

fiction readers

Requirements
Must have
• Somewhat of a dark, mysterious cover is what I'd like to see. Use your imagination. I've never written a fiction book before so I'm very open to ideas

Needs to have my name, DEREK FALLOWAY at the bottom. like my other books, all of which are non-fiction
Nice to have
• Mysterious is what I'm looking for. NOT A HORROR story though. More a guy who left the island years ago, but is being called back to escape the rat race of modern, consumerist culture.

Please remember this NEEDS to jump out as a thumbnail on Brevix as people are browsing. Mainly the WORDS need to stick out. Lighter words on a say a blue background.

If you want to try to use the attached pic, or something like this, to reflect an island in the cover, that'd be good.

I've also uploaded a couple images I purchased from Pictoravault, hopefully you can make something work with these.

```html
<!DOCTYPE html>
<html lang="en">
<head>
<meta charset="utf-8">
<title>Beyond The Grey Harbor — Book Cover</title>
<link rel="stylesheet" href="https://fonts.googleapis.com/css2?family=Anton&family=Montserrat:wght@500;700&display=swap">
<style>
  :root {
    --backdrop: #2a2622;
    --paper-light: #dcdad6;
    --paper-mid: #c9c6c1;
    --rust: #9a3a22;
    --title-grey-top: #8a8a8a;
    --title-grey-bottom: #3f3f3f;
    --title-dark: #1f1f1f;
    --author: #f2f2f2;
  }
  * { margin: 0; padding: 0; box-sizing: border-box; }
  html, body {
    width: 1200px;
    height: 901px;
    overflow: hidden;
    background: var(--backdrop);
  }
  .book-cover {
    position: absolute;
    left: 335px;
    top: 28px;
    width: 530px;
    height: 845px;
    overflow: hidden;
    background: linear-gradient(180deg, var(--paper-light) 0%, var(--paper-mid) 45%, var(--paper-mid) 100%);
    box-shadow: 0 10px 30px rgba(0,0,0,0.45);
  }
  .cover-scene {
    position: absolute;
    left: 0;
    top: 360px;
    width: 530px;
    height: 485px;
    display: block;
  }
  .title-block {
    position: absolute;
    left: 0;
    top: 0;
    width: 100%;
    height: 440px;
    text-align: center;
  }
  .title-heading {
    font-weight: normal;
  }
  .title-lead {
    position: absolute;
    left: 0;
    top: 118px;
    width: 100%;
    text-align: center;
    font-family: "Montserrat", sans-serif;
    font-weight: 500;
    font-size: 37px;
    letter-spacing: 1px;
    color: var(--rust);
  }
  .title-main {
    position: absolute;
    left: 0;
    display: block;
    width: 100%;
    text-align: center;
    font-family: "Anton", sans-serif;
    font-weight: 400;
    line-height: 1;
    text-transform: uppercase;
    white-space: nowrap;
  }
  .title-main--grey {
    top: 158px;
    font-size: 112px;
    letter-spacing: 2px;
    background: linear-gradient(180deg, var(--title-grey-top), var(--title-grey-bottom));
    -webkit-background-clip: text;
    background-clip: text;
    color: transparent;
  }
  .title-main--dark {
    top: 268px;
    font-size: 142px;
    color: var(--title-dark);
  }
  .author-line {
    position: absolute;
    left: 0;
    top: 727px;
    width: 100%;
    text-align: center;
    font-family: "Montserrat", sans-serif;
    font-weight: 700;
    font-size: 23px;
    color: var(--author);
  }
</style>
</head>
<body>
  <main class="book-cover">
    <svg class="cover-scene" role="img" aria-label="Photograph of a rocky island with red wooden houses above a dark grey sea" viewBox="0 0 530 485" preserveAspectRatio="none">
      <defs>
        <linearGradient id="sceneFade" x1="0" y1="0" x2="0" y2="1">
          <stop offset="0" stop-color="#c9c6c1" stop-opacity="0"/>
          <stop offset="0.12" stop-color="#8f7d72"/>
          <stop offset="0.3" stop-color="#6e3d2c"/>
          <stop offset="0.5" stop-color="#4a4a4a"/>
          <stop offset="0.75" stop-color="#2e2e2e"/>
          <stop offset="1" stop-color="#1e1e1e"/>
        </linearGradient>
      </defs>
      <rect width="530" height="485" fill="url(#sceneFade)"/>
    </svg>

    <header class="title-block">
      <p class="title-lead">BEYOND THE</p>
      <h1 class="title-heading">
        <span class="title-main title-main--grey">GREY</span>
        <span class="title-main title-main--dark">HARBOR</span>
      </h1>
    </header>

    <p class="author-line">By: Derek Falloway</p>
  </main>
</body>
</html>
```